Wedding filmmaker needs artistic business card design - brightwaterreels.ca

We are high end wedding filmmakers in a major market who produce cinematic wedding films. We require a business card design that communicates our quality, artistry, and professionalism yet looks progressive and friendly. Colors and design should skew appeal more to the bride-to-be who is usually the decision maker but not be overtly feminine per se. This means generally light pastel shades of ivory, purple, pink, yellow, as examples.
We already have a name logo established: the words "Brightwater Reels" in the font Great Vibes. Designs must use Kraft natural cardstock as the print stock and am leaning heavily toward our name logo in white, but I am open to black as well. Please design any color elements with spot white underneath where possible.
Do not try to compliment or take inspiration from our website design. Treat the card design as a separate stand alone.
Thank you so much for your hard work!

Target Market(s)

Affluent couples spending $50,000+ on their wedding

Industry/Entity Type

Progressive

Contact Information for Business Card

Peter Brightwater
Producer
905-482-7139
www.brightwaterreels.ca
peter@brightwaterreels.ca
twitter @brightwater287

Font styles to use
Serif
Sans Serif

Requirements
Must have
• - Brightwater Reels name logo (reference GIF uploaded for reference only) and catch phrase: Breathtaking wedding films (I'm open to capitalizing all three words, or just first, or all in small caps). I favor logo, and catch phrase on front of card and my contact details on the other side but if you feel strongly about a different design, go for it!
• - Design must be submitted shown on Kraft natural cardstock NOT WHITE cardstock, If you're not familiar with Kraft, this is what it looks like: http://www.quillandlatchjournal.com/wp-content/uploads/2013/07/il_570xN.382745196_kq3m.jpg
Nice to have
• - An original graphic element (eg. movie reel, bouquet, confetti, etc.) that compliments the name logo but is subtle and discreet, doesn't overpower or entangle it.
• -Great use of balance, composition, negative space, etc. I like clean tasteful design
Should not have
• -Lousy boring clip art.
• -Graphic elements, fonts, or color palette from our website
• -White cardstock background
• -designs you have previously submitted for other contests
• -Bold dark colors (eg. red, orange navy blue, etc.)
• -High tech futuristic designs like you'd create for a software company

```html
<!DOCTYPE html>
<html lang="en">
<head>
<meta charset="utf-8">
<title>Brightwater Reels – Business Card</title>
<link rel="stylesheet" href="https://fonts.googleapis.com/css2?family=Great+Vibes&family=Open+Sans:wght@400;700&display=swap">
<style>
  :root {
    --backdrop: #ece7e0;
    --kraft: #c9a47b;
    --kraft-shade: #bb9569;
    --band: #b8a6c6;
    --band-line: #ffffff;
    --logo: #ffffff;
    --ink: #4a3425;
    --ink-soft: #5e4636;
  }
  * { box-sizing: border-box; margin: 0; padding: 0; }
  html, body {
    width: 1200px;
    height: 828px;
    overflow: hidden;
    background: var(--backdrop);
  }
  .canvas {
    position: relative;
    width: 1200px;
    height: 828px;
  }
  .card {
    position: absolute;
    top: 266px;
    width: 520px;
    height: 297px;
    background: linear-gradient(160deg, var(--kraft) 0%, var(--kraft) 60%, var(--kraft-shade) 100%);
    box-shadow: 0 10px 26px rgba(60, 45, 30, 0.22), 0 2px 4px rgba(60, 45, 30, 0.15);
    overflow: hidden;
  }
  .card--front { left: 50px; }
  .card--back { left: 630px; }

  .wordmark {
    font-family: "Great Vibes", cursive;
    color: var(--logo);
    font-weight: 400;
    white-space: nowrap;
    line-height: 1;
  }
  .card--front .wordmark {
    position: absolute;
    left: 0; right: 0;
    top: 116px;
    text-align: center;
    font-size: 60px;
  }
  .card--back .wordmark {
    position: absolute;
    left: 22px;
    top: 158px;
    font-size: 30px;
  }

  .swoosh {
    position: absolute;
    inset: 0;
    width: 520px;
    height: 297px;
  }

  .contact {
    position: absolute;
    left: 215px;
    top: 26px;
    font-family: "Open Sans", sans-serif;
    color: var(--ink);
  }
  .contact__name {
    font-size: 14px;
    font-weight: 700;
    letter-spacing: 0.02em;
    line-height: 1.3;
  }
  .contact__role {
    font-size: 10.5px;
    color: var(--ink-soft);
  }
  .contact__address {
    font-size: 9.5px;
    line-height: 1.45;
    color: var(--ink-soft);
    margin-top: 12px;
  }
  .contact__list {
    list-style: none;
    margin-top: 10px;
    font-size: 9.5px;
    color: var(--ink-soft);
  }
  .contact__item {
    display: flex;
    align-items: center;
    gap: 6px;
    line-height: 1.65;
  }
  .contact__icon {
    width: 11px;
    height: 11px;
    flex: none;
  }

  .website {
    position: absolute;
    right: 9px;
    top: 16px;
    writing-mode: vertical-rl;
    font-family: "Open Sans", sans-serif;
    font-size: 10.5px;
    letter-spacing: 0.26em;
    color: var(--band-line);
  }
</style>
</head>
<body>
<main class="canvas">

  <section class="card card--front" aria-label="Card front">
    <h1 class="wordmark">Brightwater Reels</h1>
  </section>

  <section class="card card--back" aria-label="Card back">
    <svg class="swoosh" viewBox="0 0 520 297" aria-hidden="true">
      <path d="M440 0 C 432 140, 340 240, 60 297 L520 297 L520 0 Z" fill="var(--band)"/>
      <path d="M458 0 C 452 150, 365 255, 120 297" fill="none" stroke="var(--band-line)" stroke-width="2.6"/>
      <path d="M425 0 C 418 130, 330 228, 20 297" fill="none" stroke="var(--band)" stroke-width="1.6"/>
    </svg>

    <p class="wordmark">Brightwater Reels</p>

    <div class="contact">
      <p class="contact__name">DANIEL ASHCOMBE</p>
      <p class="contact__role">Managing Director</p>
      <p class="contact__address">12 Lakeview Court<br>Riverside Road ON</p>
      <ul class="contact__list">
        <li class="contact__item">
          <svg class="contact__icon" viewBox="0 0 12 12" aria-hidden="true">
            <path d="M2.5 1 L4.5 1 L5.3 3.6 L4 4.6 C4.6 6 6 7.4 7.4 8 L8.4 6.7 L11 7.5 L11 9.5 C11 10.4 10.3 11 9.4 11 C4.8 10.7 1.3 7.2 1 2.6 C1 1.7 1.6 1 2.5 1 Z" fill="var(--ink)"/>
          </svg>
          <span>hello@brightwaterreels.ca</span>
        </li>
        <li class="contact__item">
          <svg class="contact__icon" viewBox="0 0 12 12" aria-hidden="true">
            <rect x="0.5" y="2.5" width="11" height="7.5" fill="var(--ink)"/>
            <path d="M0.8 2.8 L6 6.8 L11.2 2.8" fill="none" stroke="var(--kraft)" stroke-width="0.9"/>
          </svg>
          <span>905 555 0142</span>
        </li>
      </ul>
    </div>

    <p class="website">www.brightwaterreels.ca</p>
  </section>

</main>
</body>
</html>
```